Business Card Design

I already have a company logo for my company. I have a logo for the manufacturer we represent. I want a professional business card design.

```html
<!DOCTYPE html>
<html lang="en">
<head>
<meta charset="utf-8">
<title>Northbeam Signal LLC – Business Card</title>
<link rel="stylesheet" href="https://fonts.googleapis.com/css2?family=Open+Sans:wght@400;600;700;800&display=swap">
<style>
  :root {
    --stage: #232325;
    --card: #1d1d21;
    --card-back: #18181b;
    --red: #e41f2b;
    --gold: #c8962a;
    --white: #f4f4f4;
    --muted: #d9d9d9;
  }
  * { box-sizing: border-box; margin: 0; padding: 0; }
  html, body { width: 1200px; height: 780px; overflow: hidden; }
  body {
    background: var(--stage);
    font-family: "Open Sans", Arial, sans-serif;
    position: relative;
  }
  .card {
    position: absolute;
    width: 525px;
    height: 300px;
    top: 240px;
    overflow: hidden;
    box-shadow: 0 18px 40px rgba(0,0,0,.45);
  }
  .card--front { left: 45px; background: var(--card); }
  .card--back { left: 630px; background: var(--card-back); }

  .card__bands { position: absolute; inset: 0; }

  .brand {
    position: absolute;
    display: flex;
    align-items: center;
    gap: 10px;
    color: var(--white);
    font-weight: 800;
    text-transform: uppercase;
    letter-spacing: .04em;
    line-height: 1.05;
  }
  .brand__mark {
    flex: none;
    width: 14px; height: 14px;
    background: var(--red);
  }
  .card--front .brand { left: 40px; top: 92px; font-size: 22px; }
  .card--back .brand { left: 0; right: 0; top: 118px; justify-content: center; font-size: 32px; }
  .brand__small { display: block; font-size: .5em; letter-spacing: .3em; }

  .contact {
    position: absolute;
    left: 292px;
    top: 104px;
    color: var(--white);
  }
  .contact__name {
    font-size: 27px;
    font-weight: 700;
    line-height: 1.1;
  }
  .contact__first { color: var(--red); }
  .contact__last { color: var(--gold); }
  .contact__role { font-size: 13px; margin: 2px 0 12px; }
  .contact__address { font-size: 12.5px; line-height: 1.45; margin-bottom: 8px; }
  .contact__list { list-style: none; font-size: 12.5px; line-height: 1.55; }
  .contact__list li { display: flex; align-items: center; gap: 7px; }
  .contact__list svg { width: 11px; height: 11px; flex: none; }

  .back__texture {
    position: absolute; inset: 0;
    background: radial-gradient(ellipse at 70% 60%, #2a2a2e 0%, #1a1a1d 70%);
  }
</style>
</head>
<body>

<section class="card card--front" aria-label="Business card front">
  <svg class="card__bands" viewBox="0 0 525 300" aria-hidden="true">
    <polygon points="262,0 525,0 525,14 276,14" fill="var(--red)"/>
    <polygon points="0,286 205,286 195,300 0,300" fill="var(--gold)"/>
    <line x1="190" y1="240" x2="290" y2="95" stroke="var(--gold)" stroke-width="1"/>
  </svg>

  <div class="brand">
    <span class="brand__mark"></span>
    <span>Northbeam<br>Signal<span class="brand__small">LLC</span></span>
  </div>

  <div class="contact">
    <h1 class="contact__name"><span class="contact__first">Tomas</span> <span class="contact__last">Verhoef</span></h1>
    <p class="contact__role">Managing Director</p>
    <p class="contact__address">1840 Meadowlane Ave. Suite 310<br>Grand Prairie, TX 75050</p>
    <ul class="contact__list">
      <li>
        <svg viewBox="0 0 24 24" aria-hidden="true"><path fill="var(--red)" d="M6.6 10.8a15 15 0 0 0 6.6 6.6l2.2-2.2a1 1 0 0 1 1-.25 11.4 11.4 0 0 0 3.6.57 1 1 0 0 1 1 1V20a1 1 0 0 1-1 1A17 17 0 0 1 3 4a1 1 0 0 1 1-1h3.5a1 1 0 0 1 1 1c0 1.25.2 2.45.57 3.57a1 1 0 0 1-.25 1z"/></svg>
        (555) 214-7730
      </li>
      <li>
        <svg viewBox="0 0 24 24" aria-hidden="true"><rect x="2" y="5" width="20" height="14" rx="2" fill="var(--red)"/><path d="M3 6l9 7 9-7" fill="none" stroke="var(--card)" stroke-width="2"/></svg>
        hello@northbeamsignal.com
      </li>
      <li>
        <svg viewBox="0 0 24 24" aria-hidden="true"><circle cx="12" cy="12" r="10" fill="var(--red)"/><path d="M2 12h20M12 2c3 3 3 17 0 20M12 2c-3 3-3 17 0 20" fill="none" stroke="var(--card)" stroke-width="1.5"/></svg>
        www.northbeamsignal.com
      </li>
    </ul>
  </div>
</section>

<section class="card card--back" aria-label="Business card back">
  <div class="back__texture" role="img" aria-label="Faint repeating brand mark pattern across the card"></div>
  <div class="brand">
    <span class="brand__mark"></span>
    <span>Northbeam Signal<span class="brand__small">LLC</span></span>
  </div>
</section>

</body>
</html>
```